Professional & attention grabbing.

A business card design, front and back. I already have a logo I will attach, but I am open to something new as well.
Things to include:
Name:
Title:
Phone:
Email:
Wanting something that is professional but attention grabbing.
Also we do a lot of work using drones on natural gas pipelines (leading the future)if you want to include any of that. I'm open to ideas.
Target Market(s)
Natural gas transmission industry / greenhouse gas mitigation industry
Industry/Entity Type
Business
Colors
Designer to choose colors to be used in the design.
Look and feel
Each slider illustrates characteristics of the customer's brand and the style your logo design should communicate.

```html
<!DOCTYPE html>
<html lang="en">
<head>
<meta charset="utf-8">
<title>Kestrel Inspections – Business Card</title>
<link rel="stylesheet" href="https://fonts.googleapis.com/css2?family=Open+Sans:ital,wght@0,400;0,600;0,700;1,400&display=swap">
<style>
  :root {
    --backdrop: #e4e2df;
    --card: #ffffff;
    --brand-red: #c21f26;
    --charcoal: #3b3b3d;
    --text-light: #ffffff;
    --muted: #555557;
  }
  * { margin: 0; padding: 0; box-sizing: border-box; }
  html, body { width: 1200px; height: 987px; overflow: hidden; }
  body {
    background: var(--backdrop);
    font-family: "Open Sans", Arial, sans-serif;
    position: relative;
  }
  .card {
    position: absolute;
    left: 293px;
    width: 615px;
    height: 351px;
    background: var(--card);
    box-shadow: 0 2px 6px rgba(0,0,0,0.25);
    overflow: hidden;
  }
  .card--front { top: 130px; }
  .card--back { top: 505px; }

  .wordmark {
    position: absolute;
    left: 0; right: 0;
    display: flex;
    align-items: center;
    justify-content: center;
    gap: 14px;
  }
  .wordmark__square { background: var(--brand-red); flex: none; }
  .wordmark__name {
    color: var(--charcoal);
    font-weight: 700;
    letter-spacing: 0.5px;
    white-space: nowrap;
  }
  .card--front .wordmark { top: 100px; }
  .card--front .wordmark__square { width: 48px; height: 48px; }
  .card--front .wordmark__name { font-size: 36px; }

  .name-band {
    position: absolute;
    top: 254px; left: 0; right: 0;
    height: 47px;
    background: var(--brand-red);
    color: var(--text-light);
    display: flex;
    align-items: center;
    justify-content: center;
    gap: 8px;
  }
  .name-band__name { font-weight: 700; font-size: 20px; letter-spacing: 0.3px; }
  .name-band__dash { font-weight: 700; font-size: 20px; }
  .name-band__title { font-size: 16px; }

  .contact-band {
    position: absolute;
    top: 305px; left: 0; right: 0; bottom: 0;
    background: var(--charcoal);
    color: var(--text-light);
    display: flex;
    align-items: center;
    justify-content: center;
    gap: 8px;
    font-size: 15px;
  }
  .contact-item { display: flex; align-items: center; gap: 5px; white-space: nowrap; }
  .contact-item svg { width: 14px; height: 14px; fill: var(--text-light); flex: none; }

  .card--back .wordmark { top: 120px; flex-direction: column; gap: 18px; }
  .card--back .wordmark__square { width: 82px; height: 82px; }
  .card--back .wordmark__name { font-size: 30px; }
  .back-web {
    position: absolute;
    top: 302px; left: 0; right: 0;
    text-align: center;
    font-style: italic;
    font-size: 15px;
    letter-spacing: 4.5px;
    color: var(--muted);
  }
</style>
</head>
<body>
  <section class="card card--front">
    <div class="wordmark">
      <span class="wordmark__square"></span>
      <span class="wordmark__name">KESTREL INSPECTIONS</span>
    </div>
    <div class="name-band">
      <span class="name-band__name">DANIEL REYES</span>
      <span class="name-band__dash">-</span>
      <span class="name-band__title">CEO/FOUNDER</span>
    </div>
    <div class="contact-band">
      <span class="contact-item">
        <svg viewBox="0 0 24 24" aria-hidden="true"><path d="M6.6 10.8a15.1 15.1 0 0 0 6.6 6.6l2.2-2.2a1 1 0 0 1 1-.25 11.4 11.4 0 0 0 3.6.57 1 1 0 0 1 1 1V20a1 1 0 0 1-1 1A17 17 0 0 1 3 4a1 1 0 0 1 1-1h3.5a1 1 0 0 1 1 1c0 1.25.2 2.45.57 3.6a1 1 0 0 1-.25 1z"/></svg>
        555 014 2290
      </span>
      <span class="contact-item">
        <svg viewBox="0 0 24 24" aria-hidden="true"><path d="M2 5h20v14H2z M2 5l10 8 10-8" fill="none" stroke="#fff" stroke-width="0"/><path d="M2 5h20l-10 8z"/><path d="M2 7l10 8 10-8v12H2z"/></svg>
        HELLO@KESTRELINSPECT.COM
      </span>
      <span class="contact-item">
        <svg viewBox="0 0 24 24" aria-hidden="true"><circle cx="12" cy="12" r="10"/><path d="M7 7c2 0 3 1 3 3s-2 2-2 4 1 3 1 5M15 4c-1 2 0 3 2 3s3 2 2 4-3 1-3 4" fill="none" stroke="#3b3b3d" stroke-width="1.8"/></svg>
        WWW.KESTRELINSPECT.COM
      </span>
    </div>
  </section>

  <section class="card card--back">
    <div class="wordmark">
      <span class="wordmark__square"></span>
      <span class="wordmark__name">KESTREL INSPECTIONS</span>
    </div>
    <p class="back-web">www.kestrelinspect.com</p>
  </section>
</body>
</html>
```